Design a poster that illustrates the six central pillars of our school district's efforts with students. The attached PDF outlines the six main competencies we aim for students to possess upon graduation. Each of the 6 has 3 bullet points for the poster as well. The title is "Profile of a Trailblazer". Our mascot is this attached winged wheel. The overall concept is that staff take kids when they are young and develop these 6 things when they graduate. Our colors are navy, red, and white. We will make this poster in a variety of sizes in offices, classrooms, and in digital spaces as well. On the PDF - ignore the column that says "Synthesis". That has nothing to do with this poster.

The district is Harlow Creek Public Schools https://www.harlowcreek-schools.example/

```html
<!DOCTYPE html>
<html lang="en">
<head>
<meta charset="utf-8">
<title>Profile of a Trailblazer – Harlow Creek Public Schools</title>
<link href="https://fonts.googleapis.com/css2?family=Antonio:wght@600;700&family=Montserrat:wght@400;500&family=Arimo:wght@400;700&display=swap" rel="stylesheet">
<style>
  :root {
    --navy: #1f2d4b;
    --red: #a11c27;
    --white: #ffffff;
    --page: #e8e8e8;
    --ink: #1b1b1b;
  }
  * { box-sizing: border-box; margin: 0; padding: 0; }
  html, body { width: 1200px; height: 814px; overflow: hidden; background: var(--page); }

  .poster {
    position: absolute;
    left: 320px; top: 11px;
    width: 1045px; height: 1478px;
    background: var(--white);
    transform: scale(0.5358);
    transform-origin: top left;
    box-shadow: 0 4px 18px rgba(0,0,0,.25);
    overflow: hidden;
  }
  .navy-column {
    position: absolute; left: 0; top: 0;
    width: 507px; height: 1239px;
    background: var(--navy);
  }

  .title {
    position: absolute; top: 62px;
    font-family: "Antonio", "Arial Narrow", sans-serif;
    font-weight: 700;
    font-size: 92px;
    line-height: 1;
    letter-spacing: -1px;
    color: var(--red);
    text-transform: uppercase;
    -webkit-text-stroke: 3px var(--white);
    paint-order: stroke fill;
    text-shadow: 4px 6px 8px rgba(0,0,0,.35);
    white-space: nowrap;
  }
  .title-left { left: 40px; }
  .title-right { left: 524px; }

  .pillar { position: absolute; }
  .pillar-left { left: 42px; width: 462px; }
  .pillar-right { left: 526px; width: 515px; }

  .pillar-name {
    font-family: "Antonio", "Arial Narrow", sans-serif;
    font-weight: 600;
    font-size: 66px;
    line-height: 1;
    margin-bottom: 30px;
  }
  .pillar-left .pillar-name { color: var(--white); }
  .pillar-right .pillar-name { color: var(--red); }

  .traits { list-style: none; position: relative; }
  .traits::before {
    content: ""; position: absolute;
    left: 8px; top: 10px; bottom: -6px;
    width: 2px;
  }
  .pillar-left .traits::before { background: rgba(255,255,255,.75); }
  .pillar-right .traits::before { background: var(--navy); }

  .trait {
    position: relative;
    padding-left: 41px;
    margin-bottom: 24px;
    font-family: "Montserrat", sans-serif;
    font-size: 20px;
    line-height: 24px;
    white-space: nowrap;
  }
  .trait:last-child { margin-bottom: 0; }
  .pillar-left .trait { color: var(--white); }
  .pillar-right .trait { color: var(--ink); font-weight: 500; }

  .tick {
    position: absolute; left: 0; top: 4px;
    width: 17px; height: 17px;
  }

  .footer-navy {
    position: absolute; left: 0; top: 1349px;
    width: 1045px; height: 97px;
    background: var(--navy);
  }
  .footer-band {
    position: absolute; left: 230px; top: 1318px;
    width: 815px; height: 121px;
    background: var(--red);
  }
  .district-mark {
    position: absolute; left: 180px; top: 1315px;
    width: 110px; height: 110px;
    border-radius: 50%;
    background: var(--white);
    border: 6px solid var(--navy);
  }
  .district {
    position: absolute; left: 358px; top: 1332px;
    font-family: "Arimo", Arial, sans-serif;
    color: var(--white);
    white-space: nowrap;
  }
  .district-name { font-weight: 700; font-size: 40px; line-height: 46px; }
  .district-motto { font-weight: 400; font-size: 33px; line-height: 40px; }
</style>
</head>
<body>
<div class="poster">
  <div class="navy-column"></div>

  <h1 class="title title-left">Profile of</h1>
  <h1 class="title title-right" aria-hidden="true">A Trailblazer</h1>

  <section class="pillar pillar-left" style="top:218px">
    <h2 class="pillar-name">Communicator</h2>
    <ul class="traits">
      <li class="trait"><svg class="tick" viewBox="0 0 17 17"><rect x="1" y="1" width="15" height="15" fill="#1f2d4b" stroke="#fff" stroke-width="1.5"/><path d="M4 9 l3 3 l6 -7" fill="none" stroke="#fff" stroke-width="1.6"/></svg>Expresses ideas clearly and<br>respectfully (written &amp; verbal).</li>
      <li class="trait"><svg class="tick" viewBox="0 0 17 17"><rect x="1" y="1" width="15" height="15" fill="#1f2d4b" stroke="#fff" stroke-width="1.5"/><path d="M4 9 l3 3 l6 -7" fill="none" stroke="#fff" stroke-width="1.6"/></svg>Listens actively and understands<br>diverse perspectives.</li>
      <li class="trait"><svg class="tick" viewBox="0 0 17 17"><rect x="1" y="1" width="15" height="15" fill="#1f2d4b" stroke="#fff" stroke-width="1.5"/><path d="M4 9 l3 3 l6 -7" fill="none" stroke="#fff" stroke-width="1.6"/></svg>Adjusts communication to suit the<br>audience and context.</li>
    </ul>
  </section>

  <section class="pillar pillar-left" style="top:548px">
    <h2 class="pillar-name">Critical Thinker</h2>
    <ul class="traits">
      <li class="trait"><svg class="tick" viewBox="0 0 17 17"><rect x="1" y="1" width="15" height="15" fill="#1f2d4b" stroke="#fff" stroke-width="1.5"/><path d="M4 9 l3 3 l6 -7" fill="none" stroke="#fff" stroke-width="1.6"/></svg>Questions, analyzes, and evaluates<br>information from multiple sources.</li>
      <li class="trait"><svg class="tick" viewBox="0 0 17 17"><rect x="1" y="1" width="15" height="15" fill="#1f2d4b" stroke="#fff" stroke-width="1.5"/><path d="M4 9 l3 3 l6 -7" fill="none" stroke="#fff" stroke-width="1.6"/></svg>Identifies and solves complex problems<br>creatively.</li>
      <li class="trait"><svg class="tick" viewBox="0 0 17 17"><rect x="1" y="1" width="15" height="15" fill="#1f2d4b" stroke="#fff" stroke-width="1.5"/><path d="M4 9 l3 3 l6 -7" fill="none" stroke="#fff" stroke-width="1.6"/></svg>Uses evidence and diverse perspectives<br>to form reasoned conclusions and make<br>informed decisions.</li>
    </ul>
  </section>

  <section class="pillar pillar-left" style="top:888px">
    <h2 class="pillar-name">Responsible</h2>
    <ul class="traits">
      <li class="trait"><svg class="tick" viewBox="0 0 17 17"><rect x="1" y="1" width="15" height="15" fill="#1f2d4b" stroke="#fff" stroke-width="1.5"/><path d="M4 9 l3 3 l6 -7" fill="none" stroke="#fff" stroke-width="1.6"/></svg>Takes ownership of actions, choices,<br>and commitments now and in future<br>aspirations.</li>
      <li class="trait"><svg class="tick" viewBox="0 0 17 17"><rect x="1" y="1" width="15" height="15" fill="#1f2d4b" stroke="#fff" stroke-width="1.5"/><path d="M4 9 l3 3 l6 -7" fill="none" stroke="#fff" stroke-width="1.6"/></svg>Takes pride in managing time,<br>resources, and self while striving to<br>meet high expectations.</li>
      <li class="trait"><svg class="tick" viewBox="0 0 17 17"><rect x="1" y="1" width="15" height="15" fill="#1f2d4b" stroke="#fff" stroke-width="1.5"/><path d="M4 9 l3 3 l6 -7" fill="none" stroke="#fff" stroke-width="1.6"/></svg>Acts with integrity while advocating<br>for themselves and others.</li>
    </ul>
  </section>

  <section class="pillar pillar-right" style="top:218px">
    <h2 class="pillar-name">Adaptable</h2>
    <ul class="traits">
      <li class="trait"><svg class="tick" viewBox="0 0 17 17"><rect x="0.5" y="0.5" width="16" height="16" fill="#1f2d4b"/><path d="M4 9 l3 3 l6 -7" fill="none" stroke="#fff" stroke-width="1.8"/></svg>Responds productively to new situations,<br>challenges, and constructive feedback.</li>
      <li class="trait"><svg class="tick" viewBox="0 0 17 17"><rect x="0.5" y="0.5" width="16" height="16" fill="#1f2d4b"/><path d="M4 9 l3 3 l6 -7" fill="none" stroke="#fff" stroke-width="1.8"/></svg>Learns from new experiences and applies<br>prior knowledge in an ever-changing world.</li>
      <li class="trait"><svg class="tick" viewBox="0 0 17 17"><rect x="0.5" y="0.5" width="16" height="16" fill="#1f2d4b"/><path d="M4 9 l3 3 l6 -7" fill="none" stroke="#fff" stroke-width="1.8"/></svg>Adjusts behavior and approach to engage<br>effectively with diverse groups and<br>environments.</li>
    </ul>
  </section>

  <section class="pillar pillar-right" style="top:568px">
    <h2 class="pillar-name">Collaborator</h2>
    <ul class="traits">
      <li class="trait"><svg class="tick" viewBox="0 0 17 17"><rect x="0.5" y="0.5" width="16" height="16" fill="#1f2d4b"/><path d="M4 9 l3 3 l6 -7" fill="none" stroke="#fff" stroke-width="1.8"/></svg>Demonstrates strong teamwork by<br>contributing effectively and cooperatively<br>toward shared goals.</li>
      <li class="trait"><svg class="tick" viewBox="0 0 17 17"><rect x="0.5" y="0.5" width="16" height="16" fill="#1f2d4b"/><path d="M4 9 l3 3 l6 -7" fill="none" stroke="#fff" stroke-width="1.8"/></svg>Listens actively and values diverse ideas<br>and perspectives.</li>
      <li class="trait"><svg class="tick" viewBox="0 0 17 17"><rect x="0.5" y="0.5" width="16" height="16" fill="#1f2d4b"/><path d="M4 9 l3 3 l6 -7" fill="none" stroke="#fff" stroke-width="1.8"/></svg>Engages respectfully, compromising and<br>leading when appropriate.</li>
    </ul>
  </section>

  <section class="pillar pillar-right" style="top:906px">
    <h2 class="pillar-name">Compassionate</h2>
    <ul class="traits">
      <li class="trait"><svg class="tick" viewBox="0 0 17 17"><rect x="0.5" y="0.5" width="16" height="16" fill="#1f2d4b"/><path d="M4 9 l3 3 l6 -7" fill="none" stroke="#fff" stroke-width="1.8"/></svg>Understands and acknowledges others'<br>feelings, perspectives, and experiences.</li>
      <li class="trait"><svg class="tick" viewBox="0 0 17 17"><rect x="0.5" y="0.5" width="16" height="16" fill="#1f2d4b"/><path d="M4 9 l3 3 l6 -7" fill="none" stroke="#fff" stroke-width="1.8"/></svg>Responds with kindness, patience, and<br>support.</li>
      <li class="trait"><svg class="tick" viewBox="0 0 17 17"><rect x="0.5" y="0.5" width="16" height="16" fill="#1f2d4b"/><path d="M4 9 l3 3 l6 -7" fill="none" stroke="#fff" stroke-width="1.8"/></svg>Seeks to connect with and contribute<br>positively to the well-being of others<br>and the community.</li>
    </ul>
  </section>

  <div class="footer-navy"></div>
  <div class="footer-band"></div>
  <div class="district-mark"></div>
  <div class="district">
    <p class="district-name">Harlow Creek Public Schools</p>
    <p class="district-motto">Excellence in Academics, Arts &amp; Athletics</p>
  </div>
</div>
</body>
</html>
```